Business Card Design

New business card design

Target Market(s)

Residential & Commercial Property Managers

Industry/Entity Type

Plumbing Services

Contact Information for Business Card

Name - Rowan Keddle, title - Director, Phone Number - 0431 286 517, email - rowan@tbk-plumbing.com.au, Company ABN - 73 215 904 386,

Font styles to use
Sans Serif

Colors
0054AA
0677BA
7BADD7
CADEEF
E8F1F8

```html
<!DOCTYPE html>
<html lang="en">
<head>
<meta charset="utf-8">
<title>TBK Plumbing Services – Business Card</title>
<link rel="stylesheet" href="https://fonts.googleapis.com/css2?family=Poppins:wght@300;400;600&display=swap">
<style>
  :root {
    --backdrop: #222222;
    --card: #1c232b;
    --blue: #2aa6e0;
    --white: #ffffff;
    --warm-grey: #8a8278;
    --muted: #6b747d;
    --deep-mark: #55606b;
  }
  * { margin: 0; padding: 0; box-sizing: border-box; }
  html, body {
    width: 1200px; height: 780px; overflow: hidden;
    background: var(--backdrop);
    font-family: "Poppins", sans-serif;
  }
  .canvas {
    position: relative; width: 1200px; height: 780px;
    display: flex; align-items: center; justify-content: center; gap: 40px;
  }
  .card {
    position: relative; width: 540px; height: 310px;
    background: var(--card);
    box-shadow: 0 18px 40px rgba(0,0,0,0.55);
  }

  /* Front */
  .front .brand {
    position: absolute; left: 40px; top: 118px; width: 220px;
  }
  .brand-name {
    display: flex; align-items: center; gap: 10px;
    font-weight: 400; font-size: 54px; line-height: 1; color: var(--white);
    letter-spacing: 1px;
  }
  .brand-dot {
    width: 14px; height: 14px; border-radius: 50%; background: var(--blue);
  }
  .brand-tagline {
    margin-top: 8px; font-weight: 300; font-size: 11px;
    letter-spacing: 7px; color: var(--muted); text-transform: lowercase;
  }
  .divider {
    position: absolute; left: 280px; top: 50px; width: 1px; height: 170px;
    background: var(--blue);
  }
  .details { position: absolute; left: 305px; top: 48px; }
  .person-name { font-size: 24px; line-height: 1.1; font-weight: 300; color: var(--warm-grey); }
  .person-name .given { font-weight: 600; color: var(--blue); }
  .person-title { font-size: 13px; font-weight: 400; color: var(--white); margin-top: 2px; }
  .contact-list { list-style: none; margin-top: 26px; }
  .contact-list li {
    display: flex; align-items: center; gap: 9px;
    font-size: 11.5px; color: var(--white); line-height: 22px;
  }
  .contact-list svg { width: 13px; height: 13px; flex: none; }
  .abn {
    position: absolute; left: 305px; bottom: 30px;
    font-size: 13px; color: var(--blue); letter-spacing: 0.5px;
  }

  /* Back */
  .back .brand {
    position: absolute; left: 0; right: 0; top: 100px; text-align: center;
  }
  .back .brand-name {
    justify-content: center; font-size: 76px; color: var(--deep-mark);
  }
  .back .brand-dot { width: 18px; height: 18px; }
  .back .brand-tagline {
    margin-top: 12px; font-size: 14px; letter-spacing: 12px; color: var(--deep-mark);
  }
</style>
</head>
<body>
<main class="canvas">

  <section class="card front" aria-label="Business card front">
    <div class="brand">
      <div class="brand-name">tbk<span class="brand-dot"></span></div>
      <div class="brand-tagline">plumbing services</div>
    </div>

    <div class="divider"></div>

    <div class="details">
      <p class="person-name"><span class="given">Rowan</span> Keddle</p>
      <p class="person-title">Director</p>
      <ul class="contact-list">
        <li>
          <svg viewBox="0 0 16 16" aria-hidden="true"><path fill="#2aa6e0" d="M3.6 1.5l2.3 2.6-1.3 1.7c.9 2 2.5 3.6 4.6 4.6l1.7-1.3 2.6 2.3-1.3 2.1C7 13.3 2.7 9 1.5 3z"/></svg>
          0431 286 517
        </li>
        <li>
          <svg viewBox="0 0 16 16" aria-hidden="true"><rect x="1.5" y="3.5" width="13" height="9" rx="1" fill="none" stroke="#2aa6e0" stroke-width="1.5"/><path d="M2 4.5l6 4.5 6-4.5" fill="none" stroke="#2aa6e0" stroke-width="1.5"/></svg>
          rowan@tbk-plumbing.com.au
        </li>
        <li>
          <svg viewBox="0 0 16 16" aria-hidden="true"><circle cx="8" cy="8" r="6.3" fill="none" stroke="#2aa6e0" stroke-width="1.5"/><path d="M1.7 8h12.6M8 1.7c-3 3.4-3 9.2 0 12.6M8 1.7c3 3.4 3 9.2 0 12.6" fill="none" stroke="#2aa6e0" stroke-width="1.2"/></svg>
          www.tbk-plumbing.com.au
        </li>
      </ul>
    </div>

    <p class="abn">ABN - 73 215 904 386,</p>
  </section>

  <section class="card back" aria-label="Business card back">
    <div class="brand">
      <div class="brand-name">tbk<span class="brand-dot"></span></div>
      <div class="brand-tagline">plumbing services</div>
    </div>
  </section>

</main>
</body>
</html>
```